Website for a Psychologist in Private Practice

I need a cool web design for my website: www.drkalvoric.com. I would like it to look professional. Keep all the current content and add: Space for video; radio spots (see Silver Cedar Tunes Logo below for those); Quick Inquiry; Friendora link; 5 star rating on Rivo; a map; reviews from former patients. I am open to suggestions.

Target Market(s)

Those seeking individual and marital counseling.

Industry/Entity Type

Mental Health

Number of Pages Required

1 page

Font styles to use
Sans Serif
Other font styles liked:
• I'm open but no hard to read script

Requirements
Must have
• All the content on my home page with link for video and radio spots. List services and degrees and expertices (pics not necessary).
Nice to have
• A video of me and radio conversations (logo of Silver Cedar Tunes radio attached).
Should not have
• Cartoons, comedy, etc.... I don't need pictures of services (marital, depression, etc...) Just list those.

```html
<!DOCTYPE html>
<html lang="en">
<head>
<meta charset="utf-8">
<title>Dr. Mara L. Kalvoric — Psychologist</title>
<link href="https://fonts.googleapis.com/css2?family=Cinzel:wght@400;700&family=Lato:ital,wght@0,400;0,700;0,900;1,400&display=swap" rel="stylesheet">
<style>
:root{
  --blue:#1a7bc1;
  --blue-band:#2f86c9;
  --green:#129a12;
  --green-dark:#0c7d0c;
  --ink:#222;
  --muted:#555;
  --rule:#cfcfcf;
  --panel:#f4f4f4;
  --footer-dark:#5b5b5b;
  --white:#fff;
}
*{margin:0;padding:0;box-sizing:border-box}
html,body{width:904px;height:1200px;overflow:hidden;background:var(--white)}
body{position:relative;font-family:'Lato',sans-serif;color:var(--ink)}
.abs{position:absolute}

/* header */
.top-line{left:0;top:0;width:904px;height:3px;background:var(--blue)}
.brand{left:58px;top:15px;font-size:33px;color:var(--blue);letter-spacing:.5px;font-family:'Cinzel',serif;white-space:nowrap}
.schedule{left:656px;top:0;width:204px;height:27px;background:var(--blue);color:#fff;font-size:12px;font-weight:700;display:flex;align-items:center;justify-content:center;gap:8px;clip-path:polygon(0 0,100% 0,96% 100%,4% 100%)}
.contact-row{top:41px;left:580px;display:flex;gap:14px;font-size:12.5px;align-items:center}
.contact-row span{display:flex;align-items:center;gap:7px}
.dot{width:20px;height:20px;border-radius:50%;background:var(--green);display:flex;align-items:center;justify-content:center}

/* nav */
.nav{left:0;top:72px;width:904px;height:34px;background:var(--green);display:flex;font-family:'Cinzel',serif;font-size:13px;color:#fff}
.nav a{color:#fff;text-decoration:none;display:flex;align-items:center;justify-content:center;border-right:1px solid rgba(0,0,0,.15);letter-spacing:.5px}
.nav a.active{background:var(--blue)}

/* hero */
.hero{left:0;top:106px;width:904px;height:345px;background:linear-gradient(90deg,#b9b4ab 0%,#d8d4cd 30%,#8e8a84 50%,#dcd8d1 70%,#c9b8a3 100%)}
.hero-title{left:0;top:350px;width:904px;text-align:center;color:#fff;font-family:'Cinzel',serif;font-size:25px;text-shadow:0 2px 4px rgba(0,0,0,.5);white-space:nowrap}
.hero-arrow{left:858px;top:262px}

/* services */
.service{top:405px;width:120px;text-align:center}
.badge{width:96px;height:96px;border-radius:50%;margin:0 auto;background:radial-gradient(circle at 55% 45%,#fff 0 58%,#f1f1f1 60%);border:5px solid var(--green);border-right-color:#e6e6e6;border-top-color:#f3f3f3}
.service p{margin-top:8px;font-size:14.5px;font-weight:700;line-height:1.25}

/* about */
.panel{left:0;top:575px;width:904px;height:265px;background:var(--panel)}
.section-title{font-family:'Cinzel',serif;color:var(--blue);font-size:19px;font-weight:400;white-space:nowrap}
.rule{height:1px;background:var(--rule)}
.about-text{left:61px;top:643px;width:490px;font-size:11.2px;line-height:18px;color:#333}
.degrees-label{left:62px;top:742px;font-family:'Cinzel',serif;font-size:18px}
.brace{left:170px;top:706px;font-size:76px;font-family:'Lato',sans-serif;font-weight:400;color:#222;line-height:1}
.checks{list-style:none;font-size:11.2px;color:#333}
.checks li{display:flex;align-items:center;gap:6px;height:21px}
.video{left:584px;top:647px;width:259px;height:156px;background:linear-gradient(135deg,#cfd6d2,#ebe6df 45%,#c7a88c 100%);box-shadow:0 6px 8px -4px rgba(0,0,0,.35)}
.video-bar{left:0;bottom:0;width:100%;height:23px;background:#1d1d1d}

/* lower sections */
.sess{font-size:10.5px;color:#222}
.sess li{list-style:none;display:flex;gap:5px;align-items:center;height:25.5px;white-space:nowrap}
.btn{background:var(--green);color:#fff;font-size:9.5px;font-weight:900;letter-spacing:.4px;display:flex;align-items:center;justify-content:center}
.field{left:367px;width:195px;height:23px;border:1px solid #9a9a9a;font-size:10px;padding:5px 7px;background:#fff}
.quote{left:598px;top:920px;width:246px;height:100px;border:1px solid #d6d6d6;border-radius:6px;font-style:italic;font-size:10px;line-height:17.6px;padding:12px 9px;color:#333;box-shadow:0 1px 3px rgba(0,0,0,.1)}

/* footer */
.footer{left:0;top:1080px;width:904px;height:89px;background:var(--blue-band);color:#fff}
.footer-links{left:61px;top:16px;display:flex;font-size:11px}
.footer-info{left:61px;top:55px;display:flex;gap:34px;font-size:12px;align-items:center;white-space:nowrap}
.footer-info span{display:flex;gap:6px;align-items:center}
.partner{top:38px;width:76px;height:34px;background:#fff;color:var(--blue);font-size:10px;font-weight:700;display:flex;align-items:center;justify-content:center}
.bottom{left:0;top:1169px;width:904px;height:31px;background:var(--footer-dark);color:#fff;font-size:10.5px}
</style>
</head>
<body>

<header>
  <div class="abs top-line"></div>
  <div class="abs brand">Dr. Mara L. Kalvoric</div>
  <div class="abs schedule">
    <svg width="16" height="16" viewBox="0 0 16 16"><rect x="1" y="3" width="12" height="11" fill="none" stroke="#fff" stroke-width="1.4"/><line x1="1" y1="6" x2="13" y2="6" stroke="#fff"/><circle cx="12" cy="12" r="3.5" fill="var(--blue)" stroke="#fff"/></svg>
    Schedule An Appointment
  </div>
  <div class="abs contact-row">
    <span><i class="dot"><svg width="10" height="8" viewBox="0 0 10 8"><rect x=".5" y=".5" width="9" height="7" fill="none" stroke="#fff"/><path d="M.5 .5 5 4.5 9.5 .5" fill="none" stroke="#fff"/></svg></i>mk@drkalvoric.com</span>
    <span><i class="dot"><svg width="10" height="10" viewBox="0 0 10 10"><path d="M2 1 4 3 3 4.5Q4.5 6.5 5.5 7L7 6 9 8 7.5 9.5Q3 9 .5 2.5Z" fill="#fff"/></svg></i>(555) 210 4837</span>
  </div>
</header>

<nav class="abs nav">
  <a class="active" style="margin-left:60px;width:71px">Home</a>
  <a style="width:107px">Bio</a>
  <a style="width:177px">My Expertise</a>
  <a style="width:143px">Sessions</a>
  <a style="width:159px">Resources</a>
  <a style="width:187px;border-right:0">Contact Me</a>
</nav>

<section>
  <div class="abs hero" role="img" aria-label="Photo of a couple in a counselling session with a therapist"></div>
  <h1 class="abs hero-title" style="font-weight:400">Helping You To&nbsp; Find Your Own Solutions</h1>
  <svg class="abs hero-arrow" width="24" height="50" viewBox="0 0 24 50"><path d="M2 2 22 25 2 48" fill="none" stroke="rgba(255,255,255,.6)" stroke-width="1.5"/></svg>

  <div class="abs service" style="left:49px"><div class="badge" role="img" aria-label="Dating icon"></div><p>Dating</p></div>
  <div class="abs service" style="left:185px"><div class="badge" role="img" aria-label="Marriage icon"></div><p>Marriage</p></div>
  <div class="abs service" style="left:322px"><div class="badge" role="img" aria-label="Professional relationship icon"></div><p>Professional<br>Relationship</p></div>
  <div class="abs service" style="left:458px"><div class="badge" role="img" aria-label="Depression and anxiety icon"></div><p>Depression &amp;<br>Anxiety Issues</p></div>
  <div class="abs service" style="left:594px"><div class="badge" role="img" aria-label="Personality disorders icon"></div><p>Personality<br>Disorders</p></div>
  <div class="abs service" style="left:730px"><div class="badge" role="img" aria-label="Life management icon"></div><p>Life<br>Management</p></div>
</section>

<section class="abs panel"></section>
<h2 class="abs section-title" style="left:60px;top:598px">About Dr. Mara L. Kalvoric</h2>
<div class="abs rule" style="left:60px;top:633px;width:482px"></div>
<p class="abs about-text">Lorem ipsum dolor sit amet, consectetuer adipiscing elit, sed diam nonummy nibh euismod tincidunt ut laoreet dolore magna aliquam erat volutpat. Ut wisi enim ad minim veniam, quis nostrud exerci tation ullamcorper suscipit lobortis nisl ut aliquip ex ea commodo consequat.</p>
<div class="abs degrees-label">My Degrees</div>
<div class="abs brace">}</div>
<ul class="abs checks" style="left:210px;top:713px">
  <li><svg width="10" height="9" viewBox="0 0 10 9"><path d="M1 5 4 8 9 1" fill="none" stroke="var(--green)" stroke-width="2"/></svg>Doctoral Degree in Clinical Psychology</li>
  <li><svg width="10" height="9" viewBox="0 0 10 9"><path d="M1 5 4 8 9 1" fill="none" stroke="var(--green)" stroke-width="2"/></svg>Masters Degree in Counseling Psychology</li>
  <li><svg width="10" height="9" viewBox="0 0 10 9"><path d="M1 5 4 8 9 1" fill="none" stroke="var(--green)" stroke-width="2"/></svg>Doctoral Internship, Coastline University Medical Center</li>
  <li><svg width="10" height="9" viewBox="0 0 10 9"><path d="M1 5 4 8 9 1" fill="none" stroke="var(--green)" stroke-width="2"/></svg>Masters Internship, Westbrook Clinic</li>
</ul>

<h2 class="abs section-title" style="left:583px;top:598px">View Video</h2>
<div class="abs rule" style="left:583px;top:633px;width:261px"></div>
<div class="abs video">
  <div class="abs" style="left:0;top:0;width:259px;height:133px" role="img" aria-label="Video still of a therapist with two clients"></div>
  <div class="abs video-bar">
    <svg width="259" height="23" viewBox="0 0 259 23">
      <path d="M10 7v9l7-4.5z" fill="#fff"/>
      <line x1="25" y1="3" x2="25" y2="20" stroke="#444"/>
      <path d="M31 9h3l4-3v11l-4-3h-3z" fill="#ccc"/>
      <rect x="46" y="10" width="180" height="4" rx="2" fill="#555"/>
      <rect x="46" y="10" width="80" height="4" rx="2" fill="#d0302a"/>
      <path d="M236 16l7-7M240 9h3v3M236 13v3h3" stroke="#ddd" fill="none"/>
    </svg>
  </div>
</div>

<section>
  <h2 class="abs section-title" style="left:60px;top:865px">My Sessions</h2>
  <div class="abs rule" style="left:60px;top:896px;width:249px"></div>
  <ul class="abs sess" style="left:60px;top:912px">
    <li><b>✔</b> Individual Sessions</li><li><b>✔</b> Marriage Sessions</li><li><b>✔</b> Family Sessions</li><li><b>✔</b> Phone Sessions</li>
  </ul>
  <ul class="abs sess" style="left:168px;top:912px">
    <li><b>✔</b> Divorce Mediation</li><li><b>✔</b> Custody Evaluation Sessions</li><li><b>✔</b> Testing Sessions</li><li><b>✔</b> Weekend / Holiday Sessions</li>
  </ul>
  <div class="abs btn" style="left:60px;top:1027px;width:75px;height:23px">READ MORE</div>

  <h2 class="abs section-title" style="left:366px;top:865px">Quick Inquiry</h2>
  <div class="abs rule" style="left:366px;top:896px;width:197px"></div>
  <div class="abs field" style="top:918px">Name</div>
  <div class="abs field" style="top:948px">Email</div>
  <div class="abs field" style="top:978px;height:40px">Message</div>
  <div class="abs btn" style="left:367px;top:1025px;width:67px;height:23px">SUBMIT</div>

  <h2 class="abs section-title" style="left:595px;top:866px;font-size:18px">Radio Conversations</h2>
  <svg class="abs" style="left:817px;top:869px" width="28" height="14" viewBox="0 0 28 14"><path d="M7 3 3 7 7 11M21 3 25 7 21 11" fill="none" stroke="#222" stroke-width="1.8"/></svg>
  <div class="abs rule" style="left:595px;top:896px;width:249px"></div>
  <div class="abs quote">Lorem ipsum dolor sit amet, consectetuer adipiscingelit, sed diam nonummy nibh euismod tinciduntttfgf dolore magna aliquam erat volutpat. tinciduntpsum dolor sit amet, consectetuer adip</div>
  <svg class="abs" style="left:690px;top:1019px" width="34" height="18" viewBox="0 0 34 18"><path d="M0 1 32 17 24 1" fill="#fff" stroke="#d6d6d6"/><line x1="1" y1="1" x2="23" y2="1" stroke="#fff" stroke-width="2"/></svg>
  <div class="abs" style="left:700px;top:1024px;width:144px;text-align:right;font-size:10.5px;font-weight:700">- Lorem ipsum dolor</div>
  <div class="abs" style="left:700px;top:1038px;width:105px;text-align:right;font-size:9px;font-style:italic;color:var(--blue)">Sitamet, CA</div>
</section>

<footer>
  <div class="abs footer">
    <div class="abs footer-links">
      <span style="width:72px">Home</span><span style="width:58px">Bio</span><span style="width:113px">My Expertise</span><span style="width:89px">Sessions</span><span style="width:100px">Resources</span><span>Contact Me</span>
    </div>
    <div class="abs" style="left:61px;top:45px;width:569px;height:1px;background:rgba(255,255,255,.35)"></div>
    <div class="abs footer-info">
      <span><svg width="10" height="10" viewBox="0 0 10 10"><path d="M2 1 4 3 3 4.5Q4.5 6.5 5.5 7L7 6 9 8 7.5 9.5Q3 9 .5 2.5Z" fill="#fff"/></svg>(555) 210 4837</span>
      <span><svg width="11" height="8" viewBox="0 0 11 8"><rect width="11" height="8" fill="#fff"/><path d="M0 0 5.5 4.5 11 0" fill="none" stroke="var(--blue-band)"/></svg>mk@drkalvoric.com</span>
      <span><svg width="8" height="11" viewBox="0 0 8 11"><path d="M4 11 0.7 5A3.8 3.8 0 1 1 7.3 5Z" fill="#fff"/><circle cx="4" cy="4" r="1.4" fill="var(--blue-band)"/></svg>418 Linden Court, Suite 120&nbsp; Harbor Vale, CA 90455</span>
    </div>
    <div class="abs" style="left:650px;top:16px;width:193px;text-align:right;font-size:11px;font-weight:700;white-space:nowrap">A portion of all revenue is donated to</div>
    <div class="abs partner" style="left:683px">Brightpath</div>
    <div class="abs partner" style="left:767px">Harbor Nest</div>
  </div>
  <div class="abs bottom">
    <div class="abs" style="left:61px;top:9px">Copyright © 2016 Dr. Mara L. Kalvoric. All Rights Reserved.</div>
    <div class="abs" style="left:730px;top:9px;width:114px;text-align:right;font-size:10px">Friendora&nbsp;&nbsp; Chirpline</div>
  </div>
</footer>

</body>
</html>
```